Stationery and Business Card Design

We need stationary design for our new company lanternfold. Lanternfold is a company that provides city apartment rentals for tourists in Athens We need business cards, letterheads for A4 and A5 and envelopes for A4 A5. The design needs to be modern, friendly and corporate.

Target Market(s)

City Tourists

Industry/Entity Type

Tourism

```html
<!DOCTYPE html>
<html lang="en">
<head>
<meta charset="utf-8">
<title>Lanternfold Apartments – Business Card</title>
<link rel="stylesheet" href="https://fonts.googleapis.com/css2?family=Raleway:wght@500;600&display=swap">
<style>
  :root {
    --brand-purple: #8b0a8b;
    --ink: #2e2e2e;
    --paper-top: #ffffff;
    --paper-bottom: #ececec;
  }
  * { margin: 0; padding: 0; box-sizing: border-box; }
  html, body {
    width: 1200px;
    height: 777px;
    overflow: hidden;
    background: #ffffff;
  }
  .business-card {
    position: relative;
    width: 1200px;
    height: 777px;
    background: linear-gradient(to bottom, var(--paper-top) 55%, var(--paper-bottom) 100%);
    font-family: "Raleway", sans-serif;
    color: var(--ink);
  }
  .brand-square {
    position: absolute;
    left: 71px;
    top: 71px;
    width: 262px;
    height: 262px;
    background: var(--brand-purple);
  }
  .brand-name {
    position: absolute;
    left: 408px;
    top: 140px;
    font-size: 104px;
    font-weight: 600;
    line-height: 1;
    color: var(--brand-purple);
    letter-spacing: -1px;
  }
  .contact-list {
    position: absolute;
    left: 90px;
    top: 510px;
    list-style: none;
  }
  .contact-list li,
  .address-block {
    font-size: 27px;
    font-weight: 500;
    line-height: 48px;
  }
  .contact-list li {
    display: flex;
    align-items: center;
    height: 48px;
  }
  .contact-icon {
    width: 26px;
    height: 26px;
    margin-right: 24px;
    flex: none;
    fill: var(--brand-purple);
  }
  .address {
    position: absolute;
    left: 618px;
    top: 510px;
    display: flex;
    align-items: flex-start;
  }
  .address .contact-icon {
    margin-top: 10px;
    margin-right: 26px;
  }
  .address-block {
    font-style: normal;
  }
</style>
</head>
<body>
  <main class="business-card">
    <div class="brand-square" aria-hidden="true"></div>
    <h1 class="brand-name">Lanternfold</h1>

    <ul class="contact-list">
      <li>
        <svg class="contact-icon" viewBox="0 0 24 24" aria-hidden="true">
          <path d="M2 5h20v14H2z" opacity="0"/>
          <path d="M2 6.5 12 13l10-6.5V5H2z"/>
          <path d="M2 9v10h20V9l-10 6.5z"/>
        </svg>
        info@lanternfoldapartments.gr
      </li>
      <li>
        <svg class="contact-icon" viewBox="0 0 24 24" aria-hidden="true">
          <path d="M6.6 10.8a15.2 15.2 0 0 0 6.6 6.6l2.2-2.2c.3-.3.7-.4 1-.2 1.1.4 2.3.6 3.6.6.6 0 1 .4 1 1V20c0 .6-.4 1-1 1A17 17 0 0 1 3 4c0-.6.4-1 1-1h3.5c.6 0 1 .4 1 1 0 1.3.2 2.5.6 3.6.1.3 0 .7-.2 1z"/>
        </svg>
        +30 (0)00 0000000
      </li>
      <li>
        <svg class="contact-icon" viewBox="0 0 24 24" aria-hidden="true">
          <path d="M7 1h10a2 2 0 0 1 2 2v18a2 2 0 0 1-2 2H7a2 2 0 0 1-2-2V3a2 2 0 0 1 2-2zm0 4v13h10V5zm5 14.5a1.2 1.2 0 1 0 0 2.4 1.2 1.2 0 0 0 0-2.4z"/>
        </svg>
        +30 (0)00 0000000
      </li>
      <li>
        <svg class="contact-icon" viewBox="0 0 24 24" aria-hidden="true">
          <circle cx="12" cy="12" r="10.5"/>
          <path d="M8 6.5c1.5.5 2 1.8 1.2 3-1 1.2-.2 2.6 1.3 2.8 1.2.2 1.4 1.6.8 2.6-.6 1.2 0 2.6 1 3.4-3.5-.2-7-3.4-6.8-7.3C5.6 9.2 6.6 7.6 8 6.5zm7.5 1c1.3-.2 2.8.5 3.6 1.8-.6.8-2 .8-2.6 0-.4-.6-.8-1.2-1-1.8z" fill="#ffffff"/>
        </svg>
        www.lanternfoldapartments.gr
      </li>
    </ul>

    <div class="address">
      <svg class="contact-icon" viewBox="0 0 24 24" aria-hidden="true">
        <path d="M12 1a8 8 0 0 0-8 8c0 6 8 14 8 14s8-8 8-14a8 8 0 0 0-8-8zm0 11a3 3 0 1 1 0-6 3 3 0 0 1 0 6z"/>
      </svg>
      <address class="address-block">
        Lanternfold Apartments<br>
        Orionos Street 12<br>
        10000 Athens<br>
        Greece
      </address>
    </div>
  </main>
</body>
</html>
```